wardrobe/costume stylist needs good business card for own business

Hi:)

I'm wanting a business card for my company. I am a freelance stylist.

I do wardrobe/costume stylist to TV commercials; Films; Fashion and Lifestyle shoots.

I'd like a design based around my name Rosalind Parfrey written nicely, maybe a colour? Up to you?!

I've attached a couple of images of business cards I like
.... be creative and have fun!

Thank you :)

Reason: I was trying to get my new business card ready for before I headed overseas Friday morning but I don't think that was realistic so I'd like to extend the deadline to give time to the project. Thank you

Hi designers:) Thank you for all your designs, I've extended the deadline until Sunday, so there's a bit more time. I've attached 3 pictures of business cards which I quite like, please take a look to see if it can be of help in your process. I like the pale plain or patterned background with dark font and the dark plain or patterned background with the pale font the motifs the feminine fonts the plain fonts I like the idea of playing with a circle or some shape on one side of the card with my name or initials as in the picture I have on my post could you play around with this idea a bit please? Thank you all for the work you've done :) Rosa

Hi I am working overseas til Saturday night sorry for no feedback until I teturn Thanks :) Rosa

Hi designers, Thank you all so much for submitting your designs, I really appreciate your input into my project :) I'm sorry I didn't get to respond to some comments, and give feedback. I didn't back from being away until later than I expected, and the deadline had passed then, so apologies. Thanks to you all again for all your really good designs :) Rosa

Target Market(s)

I am a freelance stylist my target audience is producers, production companies, photographers, directors...

Industry/Entity Type

Business

Requirements
Must have
• Rosalind Parfrey
Stylist or Wardrobe Stylist

email rosaparfrey@mailbox-example.co.nz
Mobile 0218467193

(Don't have to use the words 'email' and 'mobile')
Nice to have
• Would like it to be double sided
Like B & W
Like pale colour background with dark font or white font
Like dark colour background with pale font
Should not have
• I would prefer it not to incorporate pictures

```html
<!DOCTYPE html>
<html lang="en">
<head>
<meta charset="utf-8">
<title>Rosalind Parfrey – Wardrobe Stylist</title>
<link rel="stylesheet" href="https://fonts.googleapis.com/css2?family=Almendra+Display&family=Josefin+Sans:wght@300&display=swap">
<style>
  :root {
    --paper: #eeeeec;
    --paper-shade: #e4e4e1;
    --brown: #56250f;
    --teal: #4aa6bb;
    --rule: #8fb4bf;
  }
  html, body {
    margin: 0;
    padding: 0;
    width: 1200px;
    height: 702px;
    overflow: hidden;
    background: var(--paper);
  }
  .card {
    position: relative;
    width: 1200px;
    height: 702px;
    background: radial-gradient(ellipse at 60% 40%, var(--paper) 0%, var(--paper-shade) 100%);
    overflow: hidden;
  }
  .ornament-area {
    position: absolute;
    left: 0;
    top: 0;
    width: 480px;
    height: 702px;
    background: linear-gradient(90deg, rgba(86, 37, 15, 0.55) 0%, rgba(86, 37, 15, 0.25) 55%, rgba(86, 37, 15, 0) 100%);
  }
  .identity {
    position: absolute;
    left: 0;
    top: 0;
    width: 1200px;
    height: 702px;
  }
  .identity__name {
    font-family: "Almendra Display", serif;
    font-size: 150px;
    fill: var(--brown);
  }
  .identity__rule {
    stroke: var(--rule);
    stroke-width: 1.2;
  }
  .identity__role {
    font-family: "Josefin Sans", sans-serif;
    font-weight: 300;
    font-size: 50px;
    fill: var(--teal);
  }
</style>
</head>
<body>
<main class="card">
  <div class="ornament-area" role="img" aria-label="Dark brown flourish of curling scrolls and teardrop swirls along the left edge"></div>
  <svg class="identity" viewBox="0 0 1200 702" xmlns="http://www.w3.org/2000/svg">
    <text class="identity__name" x="487" y="366" textLength="553" lengthAdjust="spacingAndGlyphs">Rosalind Parfrey</text>
    <line class="identity__rule" x1="495" y1="395" x2="1038" y2="395"/>
    <text class="identity__role" x="505" y="453" textLength="532" lengthAdjust="spacing">WARDROBE STYLIST</text>
  </svg>
</main>
</body>
</html>
```